Business Cards for new orthopaedic surgery practice

My husband and I are starting our own orthopaedic surgery practice. We are looking for a business card that is uniform, but one will have my name/title and the other will have his. You can just create one design with my name on it for now. But when I choose your design as the winning design I will ask that you add another copy with his name/title.

We are looking for classy, simple, elite all in one. We like dark blues/a little gold/yellow. Something that goes with our logo. We want our logo incorporated. Here is all the info you need:
Business name: RV Bone & Vitality Center
Location: 38517 North Willowmere Ave
Maple Heights, FL 33418
Phone: 954-218-4063
Fax: 954-582-7341
Email: info@myrvbonecare.example

Names: Lydia Vance, M.D.
Board Certified Hand and Upper Extremity Surgeon

Ebo Dansu, M.D.
Board Certified Hip & Knee Replacement/General Orthopaedic Surgeon

Can decide what you want to put on the back. Maybe a slogan:
Grounded in Care. Centered on You

I am just going to upload our logo. The only thing is if we select you as the winning design, the location, and phone numbers may change. We will need your help to update that once fully solidified.

Industry/Entity Type

Medical

Contact Information for Business Card

Colors
0054AA
0677BA
7BADD7
CADEEF
E8F1F8
0094D4
00A9DD
6FCCEA
C7EBF8
E9F6FB

Requirements
Must have
• class, appeal,
Should not have
• We want to air on the side of masculine if we are looking at masculine vs. feminine feel. But we still want it classy, sophisticated, and something we will love

```html
<!DOCTYPE html>
<html lang="en">
<head>
<meta charset="utf-8">
<title>RV Bone &amp; Vitality Center – Business Cards</title>
<link href="https://fonts.googleapis.com/css2?family=Montserrat:wght@400;500;600;700&display=swap" rel="stylesheet">
<style>
  :root {
    --stage: #2b2b2d;
    --navy: #1b2a52;
    --navy-line: #24325c;
    --gold: #c9a45c;
    --white: #ffffff;
    --mark-faint: #d3d4df;
    --ink-soft: #2a2f45;
  }
  * { box-sizing: border-box; margin: 0; padding: 0; }
  html, body { width: 1200px; height: 875px; overflow: hidden; }
  body {
    background: var(--stage);
    font-family: "Montserrat", Arial, sans-serif;
    display: flex;
    flex-direction: column;
    align-items: center;
    justify-content: center;
    gap: 36px;
  }
  .card {
    position: relative;
    width: 680px;
    height: 388px;
    border-radius: 22px;
    overflow: hidden;
  }

  /* Back of card */
  .card--back {
    background: var(--navy);
    color: var(--white);
    display: flex;
    flex-direction: column;
    align-items: center;
    justify-content: center;
  }
  .brand {
    display: flex;
    align-items: center;
    gap: 16px;
  }
  .brand__dot {
    width: 22px; height: 22px;
    border-radius: 50%;
    background: var(--gold);
    flex: none;
  }
  .card--back .brand__name {
    font-size: 30px;
    font-weight: 600;
    letter-spacing: 0.5px;
    color: var(--white);
  }
  .card--back .tagline {
    position: absolute;
    bottom: 58px;
    left: 0; right: 0;
    text-align: center;
    font-size: 15px;
    font-weight: 700;
    letter-spacing: 0.3px;
  }

  /* Front of card */
  .card--front {
    background: var(--white);
    color: var(--navy);
  }
  .card--front .brand {
    position: absolute;
    top: 46px; left: 44px;
    gap: 10px;
    width: 210px;
  }
  .card--front .brand__dot { width: 14px; height: 14px; }
  .card--front .brand__name {
    font-size: 16px;
    font-weight: 600;
    line-height: 1.25;
    color: var(--navy);
  }
  .faint-name {
    position: absolute;
    top: 30px; right: 36px;
    width: 320px;
    text-align: right;
    font-size: 44px;
    font-weight: 600;
    line-height: 1.05;
    color: var(--mark-faint);
  }
  .doctor {
    position: absolute;
    left: 44px; top: 176px;
  }
  .doctor__name {
    font-size: 26px;
    font-weight: 700;
    color: var(--navy);
  }
  .doctor__suffix { color: var(--gold); }
  .doctor__title {
    margin-top: 4px;
    font-size: 14px;
    font-weight: 400;
    line-height: 1.3;
    color: var(--ink-soft);
  }
  .divider {
    position: absolute;
    left: 44px; right: 44px; top: 266px;
    height: 1px;
    background: var(--navy-line);
  }
  .contacts {
    position: absolute;
    left: 44px; top: 284px;
    list-style: none;
    font-size: 14px;
    color: var(--ink-soft);
  }
  .contacts li {
    display: flex;
    align-items: center;
    gap: 10px;
    line-height: 24px;
  }
  .contacts svg { width: 13px; height: 13px; fill: var(--gold); flex: none; }
  .address {
    position: absolute;
    right: 44px; top: 284px;
    text-align: right;
    font-size: 14px;
    font-style: normal;
    line-height: 22px;
    color: var(--ink-soft);
  }
</style>
</head>
<body>

  <section class="card card--back" aria-label="Card back">
    <div class="brand">
      <span class="brand__dot"></span>
      <span class="brand__name">RV Bone &amp; Vitality Center</span>
    </div>
    <p class="tagline">Grounded in Care. Centered on You</p>
  </section>

  <section class="card card--front" aria-label="Card front">
    <div class="brand">
      <span class="brand__dot"></span>
      <span class="brand__name">RV Bone &amp; Vitality Center</span>
    </div>
    <div class="faint-name" aria-hidden="true">RV Bone &amp; Vitality Center</div>

    <div class="doctor">
      <h1 class="doctor__name">Lydia Vance, <span class="doctor__suffix">M.D.</span></h1>
      <p class="doctor__title">Board Certified Hand and<br>Upper Extremity Surgeon</p>
    </div>

    <div class="divider"></div>

    <ul class="contacts">
      <li>
        <svg viewBox="0 0 16 16" aria-hidden="true"><path d="M3.5 1.5l2.5 0 1 3.5-1.6 1.2a9 9 0 0 0 4.4 4.4L11 9l3.5 1v2.5c0 1-1 2-2 2C6.5 14.5 1.5 9.5 1.5 3.5c0-1 1-2 2-2z"/></svg>
        954-218-4063
      </li>
      <li>
        <svg viewBox="0 0 16 16" aria-hidden="true"><path d="M4 1h8v4H4zM1 6h14v6h-3v3H4v-3H1zm4 4v4h6v-4z"/></svg>
        954-582-7341
      </li>
      <li>
        <svg viewBox="0 0 16 16" aria-hidden="true"><path d="M1 3h14v10H1zm1.5 1.3V5l5.5 4 5.5-4v-.7z"/></svg>
        info@myrvbonecare.example
      </li>
    </ul>

    <address class="address">
      38517 North Willowmere Ave<br>
      Maple Heights, FL 33418
    </address>
  </section>

</body>
</html>
```